Coastline Premier Retreats Business Card Design

Design a business card for Coastline Premier Retreats. Look at the website for colors and reference. Card should have logo, name, title, office number, mobile number, email, URL and a tagline like, "Luxury Hotel & Resort Email Marketing" (This might change).

https://www.coastlinepremierretreats.example

The rest I will leave up to your imagination.

Contact Information for Business Card

Logo, name, title, office number, mobile number, email, URL and a tagline like, "Luxury Hotel & Resort Email Marketing" (This might change).

```html
<!DOCTYPE html>
<html lang="en">
<head>
<meta charset="utf-8">
<title>Coastline Premier Retreats Business Card</title>
<link href="https://fonts.googleapis.com/css2?family=Montserrat:wght@400;500;700;800&display=swap" rel="stylesheet">
<style>
  :root {
    --backdrop: #232323;
    --card: #262627;
    --card-edge: #f36f21;
    --orange: #f47920;
    --white: #ffffff;
    --soft-white: #e9e9e9;
    --emboss: #3a3a3b;
  }
  * { box-sizing: border-box; margin: 0; padding: 0; }
  html, body {
    width: 1200px; height: 900px; overflow: hidden;
    background: var(--backdrop);
    font-family: 'Montserrat', sans-serif;
  }
  .stage {
    position: relative; width: 1200px; height: 900px;
    display: flex; flex-direction: column; align-items: center; justify-content: center; gap: 36px;
  }
  .card {
    position: relative; width: 720px; height: 400px;
    background: var(--card);
    border-radius: 24px;
    border-bottom: 5px solid var(--card-edge);
    box-shadow: 0 18px 40px rgba(0,0,0,.45);
    overflow: hidden;
  }
  /* back side */
  .card-back { display: flex; align-items: center; justify-content: center; }
  .brand-mark-back {
    display: flex; align-items: center; gap: 14px;
    font-weight: 800; font-size: 34px; letter-spacing: 1px; text-transform: uppercase;
    color: var(--emboss);
  }
  .brand-mark-back .square { width: 22px; height: 22px; background: var(--emboss); }

  /* front side */
  .brand-front {
    position: absolute; left: 56px; top: 150px;
    display: flex; align-items: center; gap: 12px;
    font-weight: 800; font-size: 23px; line-height: 1.15; text-transform: uppercase;
    color: var(--white); width: 290px;
  }
  .brand-front .square { flex: none; width: 18px; height: 18px; background: var(--orange); }
  .divider {
    position: absolute; left: 372px; top: 52px; width: 1px; height: 190px;
    background: var(--orange);
  }
  .contact { position: absolute; left: 396px; top: 52px; color: var(--white); }
  .person-name { font-weight: 700; font-size: 24px; color: var(--orange); letter-spacing: .5px; }
  .person-title { font-size: 14px; margin-top: 4px; color: var(--soft-white); }
  .contact-list { list-style: none; margin-top: 18px; }
  .contact-list li {
    display: flex; align-items: center; gap: 10px;
    font-size: 13px; line-height: 1; margin-bottom: 11px; color: var(--soft-white);
  }
  .contact-list svg { width: 14px; height: 14px; flex: none; fill: var(--orange); }
  .accent-band {
    position: absolute; left: 0; bottom: 0; width: 440px; height: 120px;
  }
  .tagline {
    position: absolute; right: 0; bottom: 84px; width: 270px; height: 36px;
    background: var(--white); color: #1c1c1c;
    display: flex; align-items: center; justify-content: center;
    font-weight: 500; font-size: 12.5px;
  }
</style>
</head>
<body>
<main class="stage">
  <section class="card card-back" aria-label="Card back">
    <div class="brand-mark-back"><span class="square"></span>Coastline Premier Retreats</div>
  </section>

  <section class="card card-front" aria-label="Card front">
    <div class="brand-front"><span class="square"></span>Coastline Premier Retreats</div>
    <div class="divider"></div>
    <div class="contact">
      <h1 class="person-name">DANIEL MORENO</h1>
      <p class="person-title">Managing Director</p>
      <ul class="contact-list">
        <li><svg viewBox="0 0 16 16"><path d="M2 5c0-2 2-3 6-3s6 1 6 3v1h-3V4.5H5V6H2zM4 7h8l2 6H2z"/></svg>555.201.4400</li>
        <li><svg viewBox="0 0 16 16"><path d="M4 1h8v14H4zM5.5 2.5v9h5v-9zM8 12.3a.9.9 0 100 1.8.9.9 0 000-1.8z"/></svg>555.201.7730</li>
        <li><svg viewBox="0 0 16 16"><path d="M1 3h14v10H1zM2.5 4.5v.5L8 9l5.5-4v-.5z"/></svg>dmoreno@coastlinepremierretreats.example</li>
        <li><svg viewBox="0 0 16 16"><path d="M8 1a7 7 0 100 14A7 7 0 008 1zm0 1.6c.8.8 1.5 2.4 1.7 4.4H6.3C6.5 5 7.2 3.4 8 2.6zM6.3 8.4h3.4c-.2 2-.9 3.6-1.7 4.4-.8-.8-1.5-2.4-1.7-4.4z"/></svg>www.coastlinepremierretreats.example</li>
      </ul>
    </div>
    <svg class="accent-band" viewBox="0 0 440 120" preserveAspectRatio="none" aria-hidden="true">
      <polygon points="0,86 400,26 440,0 440,36 0,120" fill="var(--orange)"/>
    </svg>
    <div class="tagline">Luxury Hotel &amp; Resort Email Marketing</div>
  </section>
</main>
</body>
</html>
```